KAJU Freightways #ALLKAJU Business Cards & Letterhead

I am looking to business cards designed for our organization. We are currently undergoing a small re-branding that is taking place. Our organization is called KAJU Freightways and we are headquartered in Phoenix, AZ. We primarily provide transportation and logistics services to the Marlow Parcel Bureau who is our largest customer. I would like to see a design that incorporates name, title, contact info, website, and address (this will be different depending on the employee). I would also like to see some color on the business card using our logo colors or a variation. I would like our logo on the back of the business card with the website displayed. The final design should communicate that we are a next generation transportation operate that focuses on being driver-first, customer-centric, innovative, and sustainable.We would also like our #ALLKAJU catch phrase incorporated as well.

Target Market(s)

Transportation & Logistics

Industry/Entity Type

Trucking Company

Contact Information for Business Card

-First and Last Name
-Position Title
-Contact Phone
-Contact Email
-Physical Address

Font styles to use
Serif

Colors

Designer to choose colors to be used in the design.

Requirements
Must have
• -KAJU logo prominently displayed
• -#ALLKAJU catch phrase used
• -Some amount of color, design gradient, etc.
• -Logo on the back with website listed (https://www.kajufreightco.example)

```html
<!DOCTYPE html>
<html lang="en">
<head>
<meta charset="utf-8">
<title>KAJU Freightways — Business Cards</title>
<link rel="stylesheet" href="https://fonts.googleapis.com/css2?family=Merriweather:ital,wght@0,400;0,700;0,900;1,400&display=swap">
<style>
  :root {
    --stage: #2a2b2d;
    --teal: #02333f;
    --green: #6cbd45;
    --pattern-green: #2c6a45;
    --paper: #f4f4f2;
    --silver: #c7cacc;
    --muted: #b9c2c5;
    --text-light: #e6ecee;
  }
  * { box-sizing: border-box; margin: 0; padding: 0; }
  html, body { width: 1200px; height: 960px; overflow: hidden; }
  body {
    background: var(--stage);
    font-family: "Merriweather", serif;
    position: relative;
  }
  .card {
    position: absolute;
    width: 700px;
    height: 400px;
    left: 250px;
    border-radius: 4px;
    overflow: hidden;
    box-shadow: 0 10px 30px rgba(0,0,0,.45);
  }
  .card--back { top: 50px; background: var(--teal); }
  .card--front { top: 500px; background: var(--teal); }

  .back-pattern {
    position: absolute; inset: 0;
    background: radial-gradient(circle at 50% 45%, rgba(44,106,69,.35), rgba(44,106,69,.18) 70%);
  }
  .back-mark {
    position: absolute;
    left: 50%; top: 40px;
    width: 200px; height: 200px;
    transform: translateX(-50%);
    border: 5px solid var(--silver);
    border-radius: 50%;
    display: flex; align-items: center; justify-content: center;
    background: var(--teal);
  }
  .back-mark__name {
    font-weight: 900;
    font-size: 46px;
    color: var(--silver);
    letter-spacing: 1px;
  }
  .back-info {
    position: absolute;
    left: 0; right: 0; bottom: 46px;
    text-align: center;
  }
  .back-info__tag {
    color: var(--green);
    font-weight: 700;
    font-size: 20px;
    letter-spacing: 3px;
  }
  .back-info__web {
    color: var(--text-light);
    font-size: 14px;
    margin-top: 10px;
    letter-spacing: .5px;
  }

  .front-art { position: absolute; inset: 0; }
  .front-mark__name {
    font-family: "Merriweather", serif;
    font-weight: 900;
    font-size: 62px;
    fill: var(--teal);
  }
  .contact {
    position: absolute;
    left: 44px; top: 92px;
    color: var(--text-light);
  }
  .contact__name {
    color: var(--green);
    font-weight: 700;
    font-size: 19px;
    letter-spacing: 2px;
    text-transform: uppercase;
  }
  .contact__title {
    color: var(--muted);
    font-size: 13px;
    font-style: italic;
    margin-top: 4px;
  }
  .contact__address {
    font-size: 13px;
    line-height: 20px;
    margin-top: 20px;
  }
  .contact__list {
    list-style: none;
    font-size: 13px;
    line-height: 21px;
    margin-top: 10px;
  }
  .contact__list li { display: flex; align-items: center; gap: 8px; }
  .contact__icon { width: 11px; height: 11px; flex: none; }
</style>
</head>
<body>

  <section class="card card--back" aria-label="Business card back">
    <div class="back-pattern" role="img" aria-label="Faint repeating brand pattern in dark green"></div>
    <div class="back-mark">
      <span class="back-mark__name">KAJU</span>
    </div>
    <div class="back-info">
      <p class="back-info__tag">#ALLKAJU</p>
      <p class="back-info__web">https://www.kajufreightco.example</p>
    </div>
  </section>

  <section class="card card--front" aria-label="Business card front">
    <svg class="front-art" width="700" height="400" viewBox="0 0 700 400" aria-hidden="true">
      <circle cx="660" cy="250" r="345" fill="var(--paper)" stroke="var(--green)" stroke-width="5"/>
      <circle cx="545" cy="235" r="130" fill="none" stroke="var(--green)" stroke-width="8"/>
      <text class="front-mark__name" x="545" y="257" text-anchor="middle">KAJU</text>
    </svg>

    <div class="contact">
      <h1 class="contact__name">Daniel Reyes</h1>
      <p class="contact__title">President</p>
      <p class="contact__address">4120 Saguaro Way<br>Phoenix, Arizona 85004</p>
      <ul class="contact__list">
        <li>
          <svg class="contact__icon" viewBox="0 0 12 12"><path d="M3 1 L5 3.5 L4 5 Q5.5 7.5 7 8 L8.5 7 L11 9 L9.5 11 Q4 10.5 1 3 Z" fill="var(--green)"/></svg>
          602-555-0148
        </li>
        <li>
          <svg class="contact__icon" viewBox="0 0 12 12"><rect x="0.5" y="2.5" width="11" height="7.5" fill="var(--green)"/><path d="M0.5 2.5 L6 7 L11.5 2.5" fill="none" stroke="var(--teal)" stroke-width="1"/></svg>
          daniel@kajufreightco.example
        </li>
        <li>
          <svg class="contact__icon" viewBox="0 0 12 12"><circle cx="6" cy="6" r="5.5" fill="var(--green)"/><path d="M0.5 6 H11.5 M6 0.5 V11.5" stroke="var(--teal)" stroke-width="1"/></svg>
          www.kajufreightco.example
        </li>
      </ul>
    </div>
  </section>

</body>
</html>
```